Zestora - Landing Page

Need a landing page for a journal app. The app is based on a retrospective board, where each journal entry is split into 3 sections: "What went well", "What Didn't Go Well" and "Things To Try".
The landing page should match the style of all modern web application landing pages. Think Brint, Tivalo, Mirvane. I've included screenshots of the app.
One feature that I want to highlight that is not ready yet, is an AI coach. It will offer insights based on the history of the user's journal entries
1 page

```html
<!DOCTYPE html>
<html lang="en">
<head>
<meta charset="utf-8">
<title>Zestora – Landing Page</title>
<link href="https://fonts.googleapis.com/css2?family=Outfit:wght@400;500;600&display=swap" rel="stylesheet">
<style>
:root{
  --green:#15b982;
  --ink:#161b22;
  --body:#3b4149;
  --muted:#8a9099;
  --tint:#eff9fb;
  --yellow:#fdd877;
  --pink:#fd8aa7;
  --mint:#4cf0a9;
  --line:#e3e8ec;
  --white:#ffffff;
}
*{box-sizing:border-box;margin:0;padding:0}
html,body{width:1200px;height:4345px;overflow:hidden}
body{font-family:"Outfit",sans-serif;color:var(--ink);background:var(--white);position:relative}
.abs{position:absolute}
a{color:inherit;text-decoration:none}

/* header */
.site-header{position:absolute;top:0;left:0;width:1200px;height:100px}
.brand{position:absolute;display:flex;align-items:center;gap:10px;font-weight:600;font-size:20px;color:var(--ink)}
.brand-dot{width:14px;height:14px;border-radius:50%;background:var(--green)}
.nav-link{position:absolute;top:43px;font-size:14px;color:var(--ink)}
.nav-link.has-menu::after{content:"";display:inline-block;width:5px;height:5px;border-right:1.5px solid var(--ink);border-bottom:1.5px solid var(--ink);transform:rotate(45deg);margin-left:7px;position:relative;top:-3px}
.nav-sep{position:absolute;left:906px;top:42px;width:1px;height:20px;background:#c9ced4}
.btn{display:flex;align-items:center;justify-content:center;font-size:13px;font-weight:500;letter-spacing:.2px;border-radius:3px;text-transform:uppercase}
.btn-primary{background:var(--green);color:var(--white)}
.btn-outline{border:1.5px solid var(--green);color:var(--green);background:var(--white)}

/* hero */
.hero-title{position:absolute;left:0;top:104px;width:1200px;text-align:center;font-size:52px;font-weight:500;line-height:56px}
.hero-sub{position:absolute;left:0;top:234px;width:1200px;text-align:center;font-size:18px;line-height:31px;color:var(--body)}
.tint-band{position:absolute;left:0;top:658px;width:1200px;height:1800px;background:var(--tint)}

/* app mockup */
.mockup{position:absolute;left:257px;top:393px;width:685px;height:535px;border-radius:8px;background:linear-gradient(135deg,#cfe7dd,#b9dccf);overflow:hidden}
.mock-app{position:absolute;left:22px;top:22px;width:641px;height:491px;background:#f5f7f9;border-radius:4px}
.mock-top{position:absolute;left:0;top:0;width:641px;height:34px;background:var(--white);border-bottom:1px solid var(--line)}
.mock-tiny{font-size:6px;color:var(--muted);position:absolute}
.mock-side{position:absolute;left:0;top:34px;width:108px;height:457px;background:var(--white)}
.mock-pill{position:absolute;left:18px;width:74px;height:18px;border-radius:3px;background:var(--green);color:var(--white);font-size:6px;display:flex;align-items:center;justify-content:center}
.mock-menu{position:absolute;left:22px;font-size:6px;color:var(--muted);display:flex;align-items:center;gap:6px}
.mock-menu i{width:7px;height:7px;border-radius:2px;background:#cfd5db;display:block}
.mock-head{position:absolute;left:20px;font-size:7px;color:#3d7cd4;font-weight:600}
.mock-list{position:absolute;left:124px;top:48px;width:139px;height:418px;background:var(--white);border-radius:4px}
.mock-row{position:absolute;left:12px;display:flex;align-items:center;gap:6px;font-size:6px;color:#2f4ea5}
.mock-row i{width:11px;height:11px;border-radius:50%;display:block}
.mock-chat{position:absolute;left:274px;top:48px;width:304px;height:418px;background:var(--white);border-radius:4px}
.bubble{position:absolute;font-size:5px;line-height:7px;padding:5px 7px;border-radius:4px}
.bubble.in{background:var(--white);border:1px solid var(--line);color:var(--body)}
.bubble.out{background:var(--green);color:var(--white)}
.avatar{position:absolute;width:14px;height:14px;border-radius:50%;background:#d4dbe2}

/* features */
.feature-label{position:absolute;font-size:13px;font-weight:600;color:var(--green)}
.feature-title{position:absolute;font-size:42px;font-weight:500;line-height:50px;width:450px}
.bullets{position:absolute;list-style:none;width:410px}
.bullets li{position:absolute;left:0;font-size:17px;line-height:25px;color:var(--body);padding-left:17px;width:410px}
.bullets li::before{content:"";position:absolute;left:0;top:8px;border-left:6px solid #f5b62c;border-top:5px solid transparent;border-bottom:5px solid transparent}
.blob{position:absolute}
.phone{position:absolute;background:#111;border-radius:22px;padding:7px}
.phone-screen{width:100%;height:100%;background:var(--white);border-radius:16px;position:relative;overflow:hidden}
.phone-notch{position:absolute;top:0;left:50%;transform:translateX(-50%);width:70px;height:10px;background:#111;border-radius:0 0 8px 8px}
.phone-title{position:absolute;left:12px;top:22px;font-size:9px;color:var(--ink);display:flex;gap:6px;align-items:center}
.phone-title i{width:7px;height:7px;background:#3d7cd4;border-radius:2px;display:block}
.phone-editor{position:absolute;left:10px;right:10px;top:42px;bottom:0;border:1px solid var(--line)}
.toolbar{height:30px;border-bottom:1px solid var(--line);font-size:7px;padding:4px 6px;color:var(--ink);line-height:11px}
.phone-editor ul{padding:8px 8px 0 16px;font-size:8.5px;line-height:11px;color:var(--ink)}

/* pillars */
.pillars{position:absolute;left:0;top:2458px;width:1200px;height:656px;background:var(--green)}
.pillars-title{position:absolute;left:0;top:76px;width:1200px;text-align:center;color:var(--white);font-size:40px;font-weight:500}
.pillar{position:absolute;top:184px;width:245px;height:385px;border:1.5px solid rgba(255,255,255,.75);border-radius:12px;color:var(--white)}
.pillar-icon{position:absolute;left:18px;top:18px;width:46px;height:46px}
.pillar-kicker{position:absolute;left:18px;top:85px;font-size:11px;font-weight:600;color:#fff1a8;text-transform:uppercase}
.pillar-title{position:absolute;left:18px;top:110px;width:212px;font-size:23px;line-height:32px;font-weight:500}
.pillar-text{position:absolute;left:18px;top:198px;width:200px;font-size:16px;line-height:26.5px;color:#eafff5}

/* stats */
.stats-kicker{position:absolute;left:0;top:3210px;width:1200px;text-align:center;font-size:13px;font-weight:600;color:var(--green)}
.stats-title{position:absolute;left:0;top:3232px;width:1200px;text-align:center;font-size:42px;font-weight:500}
.stat{position:absolute;top:3338px;width:200px;text-align:center}
.stat-art{width:68px;height:68px;margin:0 auto;border-radius:14px}
.stat-num{margin-top:26px;font-size:21px;font-weight:600;color:var(--green)}
.stat-label{font-size:14px;color:var(--body);margin-top:1px}

/* cta */
.cta{position:absolute;left:0;top:3575px;width:1200px;height:366px;background:var(--tint)}
.cta-title{position:absolute;left:0;top:78px;width:1200px;text-align:center;font-size:42px;font-weight:500;line-height:47px}
.cta-rating{position:absolute;left:0;top:190px;width:1200px;text-align:center;font-size:19px;color:var(--ink)}
.cta-rating b{color:var(--green);font-weight:500}
.stars{color:#f5b62c;letter-spacing:1px}

/* footer */
.foot-text{position:absolute;left:84px;top:4070px;font-size:14px;line-height:23px;color:var(--body);width:270px}
.foot-col{position:absolute;top:4012px}
.foot-col h4{font-size:14px;font-weight:500;margin-bottom:24px}
.foot-col a{display:block;font-size:14px;color:var(--body);line-height:33px}
.social{position:absolute;left:1098px;width:12px;height:12px;border-radius:50%;background:var(--ink)}
.foot-rule{position:absolute;left:84px;top:4262px;width:1030px;height:1px;background:#d6dbe0}
.foot-small{position:absolute;top:4302px;font-size:12px;color:var(--body)}
.foot-small span{color:var(--green)}
</style>
</head>
<body>

<header class="site-header">
  <a class="brand" style="left:84px;top:38px"><span class="brand-dot"></span>Zestora</a>
  <a class="nav-link has-menu" style="left:407px">Features</a>
  <a class="nav-link has-menu" style="left:511px">Solutions</a>
  <a class="nav-link has-menu" style="left:614px">Enterprise</a>
  <a class="nav-link has-menu" style="left:725px">Resources</a>
  <a class="nav-link" style="left:838px">Pricing</a>
  <span class="nav-sep"></span>
  <a class="nav-link" style="left:927px">Login</a>
  <a class="btn btn-primary abs" style="left:993px;top:32px;width:121px;height:39px">Ger started</a>
</header>

<div class="tint-band"></div>

<section class="hero">
  <h1 class="hero-title">App is based on a<br>retrospective board</h1>
  <p class="hero-sub">Curabitur mollis urna nec tellus congue, vitae hendrerit libero porta.<br>Pellentesque semper velit faucibus venenatis.</p>
  <a class="btn btn-primary abs" style="left:523px;top:309px;width:154px;height:48px">Ger started</a>

  <div class="mockup">
    <div class="mock-app">
      <div class="mock-top">
        <span class="abs" style="left:18px;top:12px;font-size:7px;font-weight:600">Lorem Ipsum</span>
        <span class="abs" style="left:120px;top:9px;width:148px;height:16px;border-radius:8px;background:#f1f3f5"></span>
        <span class="mock-tiny" style="left:130px;top:14px">Search here...</span>
        <span class="avatar" style="left:612px;top:10px"></span>
      </div>
      <div class="mock-side">
        <div class="mock-pill" style="top:52px">Select Project</div>
        <div class="mock-head" style="top:94px">Menu</div>
        <div class="mock-menu" style="top:120px"><i></i>Home</div>
        <div class="mock-menu" style="top:157px;color:#3d7cd4"><i style="background:#3d7cd4"></i>Messages</div>
        <div class="mock-menu" style="top:193px"><i></i>Document</div>
        <div class="mock-menu" style="top:230px"><i></i>Application</div>
        <div class="mock-head" style="top:267px">Configuration</div>
        <div class="mock-menu" style="top:296px"><i></i>Stack dev</div>
        <div class="mock-menu" style="top:330px"><i></i>Settings</div>
        <div class="mock-pill" style="top:404px;height:32px">Create Project</div>
      </div>
      <div class="mock-list">
        <div class="mock-row" style="top:8px;font-weight:600">Group Chat</div>
        <div class="mock-row" style="top:34px"><i style="background:#3fc37b"></i>Ann Doe</div>
        <div class="mock-row" style="top:60px"><i style="background:#f59a3c"></i>Bella Doe</div>
        <div class="mock-row" style="top:85px"><i style="background:#3d7cd4"></i>Christ Doe</div>
        <div class="mock-row" style="top:110px"><i style="background:#e7476b"></i>Donna Doe</div>
        <div class="mock-row" style="top:136px"><i style="background:#8a5cd6"></i>Ella Doe</div>
        <div class="mock-row" style="top:176px;font-weight:600">Group Chat</div>
        <div class="mock-row" style="top:212px"><i style="background:#d4dbe2"></i>Alex Doe</div>
        <div class="mock-row" style="top:254px"><i style="background:#d4dbe2"></i>Cole Doe</div>
        <div class="mock-row" style="top:296px"><i style="background:#d4dbe2"></i>James Doe</div>
        <div class="mock-row" style="top:338px"><i style="background:#d4dbe2"></i>Sara Doe</div>
      </div>
      <div class="mock-chat">
        <span class="avatar" style="left:10px;top:14px;width:20px;height:20px;background:#3d7cd4"></span>
        <span class="abs" style="left:38px;top:14px;font-size:7px;color:#2f4ea5;font-weight:600">Christ Doe</span>
        <span class="mock-tiny" style="left:38px;top:24px">Recently active</span>
        <span class="avatar" style="left:12px;top:60px"></span>
        <div class="bubble in" style="left:32px;top:58px;width:170px">Lorem ipsum dolor sit amet, sed do tempor incidunt ut labore et dolore magna aliqua.</div>
        <div class="bubble out" style="left:92px;top:120px;width:170px">Ut enim ad minim veniam, quis nostrud exercitation ullamco laboris nisi ut aliquip.</div>
        <span class="avatar" style="left:270px;top:122px"></span>
        <div class="bubble out" style="left:118px;top:160px;width:144px">Duis aute irure dolor in reprehenderit</div>
        <div class="bubble out" style="left:176px;top:184px;width:86px">Velit esse cillum</div>
        <span class="avatar" style="left:12px;top:232px"></span>
        <div class="bubble in" style="left:32px;top:230px;width:170px">Excepteur sint occaecat cupidatat non proident, sunt in culpa.</div>
        <div role="img" aria-label="Small illustration of two people chatting" class="abs" style="left:36px;top:268px;width:80px;height:56px;border-radius:6px;background:linear-gradient(135deg,#fde6c8,#cde3f7)"></div>
        <div class="abs" style="left:8px;top:342px;width:288px;height:38px;border:1px solid #b9c6f0;border-radius:4px;font-size:5px;color:var(--body);padding:6px">Lorem ipsum dolor sit amet, consectetur adipiscing elit tempor.</div>
        <div class="mock-pill" style="left:8px;top:390px;width:50px;height:14px">Send</div>
      </div>
    </div>
  </div>
</section>

<section class="feature">
  <svg class="blob" style="left:574px;top:996px" width="473" height="430" viewBox="0 0 473 430" aria-hidden="true"><path d="M380 10C450 10 480 80 460 140C430 230 300 360 190 410C110 445 10 400 2 300C-5 220 50 170 120 120C210 55 300 10 380 10Z" fill="var(--yellow)"/></svg>
  <div class="phone" style="left:700px;top:1004px;width:212px;height:322px">
    <div class="phone-screen">
      <span class="phone-notch"></span>
      <div class="phone-title"><i></i>What Went Well?</div>
      <div class="phone-editor">
        <div class="toolbar">Normal &nbsp;⇕ &nbsp; <b>B</b> <i>I</i> U S ❞<br>≡ ≡ ≡ ≡ &nbsp; T</div>
        <ul><li>Completed all scheduled workouts this week.</li><li>Increased bench press weight by 10 pounds.</li><li>Maintained consistent energy levels throughout sessions.</li></ul>
      </div>
    </div>
  </div>
  <p class="feature-label" style="left:153px;top:1052px">What went well</p>
  <h2 class="feature-title" style="left:153px;top:1072px">Vivamus eu efficitur sagittis congue</h2>
  <ul class="bullets" style="left:153px;top:1202px">
    <li style="top:0">Completed all scheduled workouts this week.</li>
    <li style="top:39px">Increased bench press weight by 10 pounds.</li>
    <li style="top:79px">Maintained consistent energy levels throughout sessions.</li>
  </ul>
</section>

<section class="feature">
  <svg class="blob" style="left:135px;top:1469px" width="476" height="421" viewBox="0 0 476 421" aria-hidden="true"><path d="M90 10C160 -10 250 50 330 120C420 200 480 260 475 330C470 400 400 430 320 410C210 380 80 290 25 210C-20 140 20 30 90 10Z" fill="var(--pink)"/></svg>
  <div class="phone" style="left:273px;top:1440px;width:222px;height:450px">
    <div class="phone-screen">
      <span class="phone-notch"></span>
      <div class="phone-title"><i></i>What Didn't Go Well?</div>
      <div class="phone-editor">
        <div class="toolbar">Normal &nbsp;⇕ &nbsp; <b>B</b> <i>I</i> U S ❞<br>≡ ≡ ≡ ≡ &nbsp; T</div>
        <ul><li>Struggled with form on deadlifts, leading to lower back discomfort.</li><li>Missed two stretching sessions after workouts.</li><li>Skipped meal prep, resulting in inconsistent nutrition.</li></ul>
      </div>
    </div>
  </div>
  <p class="feature-label" style="left:641px;top:1521px">What Didn't Go Well?</p>
  <h2 class="feature-title" style="left:641px;top:1541px">Vivamus eu efficitur sagittis congue</h2>
  <ul class="bullets" style="left:641px;top:1671px">
    <li style="top:0">Struggled with form on deadlifts, leading to lower back discomfort.</li>
    <li style="top:71px">Missed two stretching sessions after workouts.</li>
    <li style="top:110px">Skipped meal prep, resulting in inconsistent nutrition.</li>
  </ul>
</section>

<section class="feature">
  <svg class="blob" style="left:582px;top:1929px" width="476" height="426" viewBox="0 0 476 426" aria-hidden="true"><path d="M380 8C450 0 485 70 470 140C445 240 300 370 190 410C110 440 10 400 2 300C-5 220 60 170 130 120C220 55 310 15 380 8Z" fill="var(--mint)"/></svg>
  <div class="phone" style="left:692px;top:1941px;width:225px;height:322px">
    <div class="phone-screen">
      <span class="phone-notch"></span>
      <div class="phone-title"><i></i>Things To Try</div>
      <div class="phone-editor">
        <div class="toolbar">Normal &nbsp;⇕ &nbsp; <b>B</b> <i>I</i> U S ❞<br>≡ ≡ ≡ ≡ &nbsp; T</div>
        <ul><li>Focus on deadlift form by lowering the weight and reviewing proper technique.</li><li>Set reminders for post-workout stretching to prevent muscle tightness.</li><li>Dedicate Sunday evenings to meal prep to ensure a balanced diet.</li></ul>
      </div>
    </div>
  </div>
  <p class="feature-label" style="left:153px;top:1984px">Things To Try</p>
  <h2 class="feature-title" style="left:153px;top:2004px">Class aptent taciti sociosqu ad litora</h2>
  <ul class="bullets" style="left:153px;top:2125px">
    <li style="top:0">Focus on deadlift form by lowering the weight and reviewing proper technique.</li>
    <li style="top:64px">Set reminders for post-workout stretching to prevent muscle tightness.</li>
    <li style="top:127px">Dedicate Sunday evenings to meal prep to ensure a balanced diet.</li>
  </ul>
</section>

<section class="pillars">
  <h2 class="pillars-title">Interdum et malesuada fames</h2>
  <article class="pillar" style="left:84px">
    <svg class="pillar-icon" viewBox="0 0 46 46" aria-hidden="true"><circle cx="23" cy="23" r="18" fill="none" stroke="#fff" stroke-width="2"/><path d="M15 23l6 6 10-12" fill="none" stroke="#fff" stroke-width="2.5"/></svg>
    <p class="pillar-kicker">Rapid implementation</p>
    <h3 class="pillar-title">Nullam eget eros sagittis suscipit</h3>
    <p class="pillar-text">Phasellus molestie, velit et rutrum tincidunt, magna elit laoreet leo, non auctor ante tutellus. Pellentesque ut tortor at nisi sollicitudin ornare</p>
  </article>
  <article class="pillar" style="left:346px">
    <svg class="pillar-icon" viewBox="0 0 46 46" aria-hidden="true"><ellipse cx="23" cy="12" rx="12" ry="5" fill="none" stroke="#fff" stroke-width="2"/><path d="M11 12v20c0 3 5 5 12 5s12-2 12-5V12M11 22c0 3 5 5 12 5s12-2 12-5" fill="none" stroke="#fff" stroke-width="2"/></svg>
    <p class="pillar-kicker">360° Data control</p>
    <h3 class="pillar-title">Curabitur aliquam condimentum</h3>
    <p class="pillar-text">Phasellus molestie, velit et rutrum tincidunt, magna elit laoreet leo, non auctor ante tutellus. Pellentesque ut tortor at nisi sollicitudin ornare</p>
  </article>
  <article class="pillar" style="left:608px">
    <svg class="pillar-icon" viewBox="0 0 46 46" aria-hidden="true"><circle cx="23" cy="20" r="14" fill="none" stroke="#fff" stroke-width="2"/><path d="M12 40h22" stroke="#fff" stroke-width="2"/></svg>
    <p class="pillar-kicker">Delightful expeience</p>
    <h3 class="pillar-title">Praesent ac sapien id tellus viverra</h3>
    <p class="pillar-text">Phasellus molestie, velit et rutrum tincidunt, magna elit laoreet leo, non auctor ante tutellus. Pellentesque ut tortor at nisi sollicitudin ornare</p>
  </article>
  <article class="pillar" style="left:869px">
    <svg class="pillar-icon" viewBox="0 0 46 46" aria-hidden="true"><circle cx="23" cy="23" r="9" fill="none" stroke="#fff" stroke-width="2"/><path d="M4 4l8 8M42 4l-8 8M4 42l8-8M42 42l-8-8" stroke="#fff" stroke-width="2"/></svg>
    <p class="pillar-kicker">AI coach · coming soon</p>
    <h3 class="pillar-title">Insights from your journal history</h3>
    <p class="pillar-text">Your AI coach reads past entries, spots patterns in what went well and what didn't, and suggests new things to try each week.</p>
  </article>
</section>

<section class="stats">
  <p class="stats-kicker">Integer consequat</p>
  <h2 class="stats-title">Class aptent taciti socios</h2>
  <div class="stat" style="left:40px"><div class="stat-art" role="img" aria-label="Illustration of a smartphone" style="background:linear-gradient(135deg,#c9d6ff,#8fa8f0)"></div><p class="stat-num">30+ million</p><p class="stat-label">app downloads</p></div>
  <div class="stat" style="left:263px"><div class="stat-art" role="img" aria-label="Illustration of a task checklist clipboard" style="background:linear-gradient(135deg,#cfe3f7,#f5a25a)"></div><p class="stat-num">2+ billion</p><p class="stat-label">tasks completed</p></div>
  <div class="stat" style="left:479px"><div class="stat-art" role="img" aria-label="Illustration of a group of users" style="background:linear-gradient(135deg,#e4e8ee,#b9c2cf)"></div><p class="stat-num">1+ million</p><p class="stat-label">Pro users</p></div>
  <div class="stat" style="left:712px"><div class="stat-art" role="img" aria-label="Illustration of a globe" style="background:linear-gradient(135deg,#8fd3f5,#f5d45a)"></div><p class="stat-num">160+ countries</p><p class="stat-label">worldwide</p></div>
  <div class="stat" style="left:955px"><div class="stat-art" role="img" aria-label="Illustration of a happy customer with stars" style="background:linear-gradient(135deg,#fde7a0,#7fd6a2)"></div><p class="stat-num">5+ million</p><p class="stat-label">Happy customer</p></div>
</section>

<section class="cta">
  <h2 class="cta-title">Gain calmness and clarity with<br>the world’s most beloved productivity app</h2>
  <p class="cta-rating"><b>546000+</b> <span class="stars">★★★★★</span> reviews on Playway and AppHarbor</p>
  <a class="btn btn-primary abs" style="left:442px;top:250px;width:152px;height:49px">Ger started</a>
  <a class="btn btn-outline abs" style="left:604px;top:250px;width:154px;height:49px">Download app</a>
</section>

<footer>
  <a class="brand" style="left:84px;top:4018px"><span class="brand-dot"></span>Zestora</a>
  <p class="foot-text">Join millions of people who organize work and life with Zestora</p>
  <nav class="foot-col" style="left:501px"><h4>Useful Links</h4><a>Features</a><a>Solutions</a><a>Enterprise</a><a>Resources</a><a>Pricing</a></nav>
  <nav class="foot-col" style="left:704px"><h4>Resources</h4><a>Features</a><a>Solutions</a><a>Enterprise</a><a>Resources</a><a>Pricing</a></nav>
  <nav class="foot-col" style="left:911px"><h4>Company</h4><a>About Us</a><a>Careers</a><a>Inspiration Hub</a></nav>
  <span class="social" style="top:4028px"></span>
  <span class="social" style="top:4065px"></span>
  <span class="social" style="top:4102px"></span>
  <span class="social" style="top:4139px"></span>
  <div class="foot-rule"></div>
  <p class="foot-small" style="left:84px">© 2024 <span>Zestora</span>. All right reserved</p>
  <p class="foot-small" style="right:86px">August 29, 2024. Layout_4</p>
</footer>

</body>
</html>
```